"Harbor Builders" is a residential building company and needs a new business card design and may re

We would like a redesign based on the existing logo, and would like to see a new font as well. We are bespoke home builders who build sustainable energy efficient homes.

Industry/Entity Type

Construction

Contact Information for Business Card

Business card size 40mm x 90mm

Colors

Designer to choose colors to be used in the design.

```html
<!DOCTYPE html>
<html lang="en">
<head>
<meta charset="utf-8">
<title>Harbor Builders – Business Card</title>
<link rel="stylesheet" href="https://fonts.googleapis.com/css2?family=Montserrat:wght@700&family=Work+Sans:wght@400;500&display=swap">
<style>
  :root {
    --navy: #233a85;
    --orange: #f07f1d;
    --ink: #3c3c3c;
    --white: #ffffff;
    --backdrop: #2b2b2d;
  }
  * { box-sizing: border-box; margin: 0; padding: 0; }
  html, body { width: 1200px; height: 900px; overflow: hidden; }
  body {
    background: var(--backdrop);
    font-family: "Work Sans", sans-serif;
    position: relative;
  }
  .card {
    position: absolute;
    width: 700px;
    height: 390px;
    left: 250px;
    border-radius: 18px;
    overflow: hidden;
  }
  .card-back { top: 40px; background: var(--navy); }
  .card-front { top: 470px; background: var(--white); }

  .brand {
    display: flex;
    align-items: center;
    gap: 16px;
    font-family: "Montserrat", sans-serif;
    font-weight: 700;
    font-size: 34px;
    letter-spacing: 1px;
    text-transform: uppercase;
  }
  .brand-mark { width: 34px; height: 34px; flex: none; }
  .card-back .brand {
    position: absolute; left: 50%; top: 50%;
    transform: translate(-50%, -50%);
    color: var(--white);
    white-space: nowrap;
  }
  .card-back .brand-mark { border: 5px solid var(--white); }
  .card-front .brand {
    position: absolute; left: 48px; top: 52px;
    color: var(--navy);
  }
  .card-front .brand-mark { background: var(--orange); }

  .divider {
    position: absolute; left: 48px; right: 60px; top: 232px;
    height: 2px; background: var(--orange);
  }
  .person {
    position: absolute; right: 60px; top: 166px; text-align: right;
  }
  .person-name {
    font-family: "Montserrat", sans-serif; font-weight: 700;
    font-size: 24px; color: var(--navy); letter-spacing: 0.5px;
  }
  .person-role { font-size: 17px; font-weight: 500; color: #222; margin-top: 2px; }

  .contact-list {
    position: absolute; left: 48px; top: 252px;
    list-style: none; font-size: 17px; color: var(--ink); line-height: 26px;
  }
  .contact-list li { display: flex; align-items: center; gap: 12px; }
  .contact-list svg { width: 15px; height: 15px; fill: var(--orange); flex: none; }

  .address {
    position: absolute; right: 60px; top: 252px; text-align: right;
    font-size: 17px; color: var(--ink); line-height: 26px;
  }
  .address .label { color: var(--navy); font-weight: 500; }

  .edge-tab {
    position: absolute; right: 0; top: 168px;
    width: 10px; height: 62px; background: var(--orange);
    border-radius: 6px 0 0 6px;
  }
  .base-band { position: absolute; left: 0; bottom: 0; width: 700px; height: 22px; }
</style>
</head>
<body>
  <section class="card card-back" aria-label="Card back">
    <div class="brand"><span class="brand-mark"></span>Harbor Builders</div>
  </section>

  <section class="card card-front" aria-label="Card front">
    <div class="brand"><span class="brand-mark"></span>Harbor Builders</div>

    <div class="person">
      <p class="person-name">DANIEL MORETTI</p>
      <p class="person-role">Founder</p>
    </div>
    <div class="divider"></div>

    <ul class="contact-list">
      <li><svg viewBox="0 0 24 24"><path d="M6.6 10.8a15.1 15.1 0 0 0 6.6 6.6l2.2-2.2a1 1 0 0 1 1-.25 11.4 11.4 0 0 0 3.6.57 1 1 0 0 1 1 1V20a1 1 0 0 1-1 1A17 17 0 0 1 3 4a1 1 0 0 1 1-1h3.5a1 1 0 0 1 1 1c0 1.25.2 2.45.57 3.57a1 1 0 0 1-.25 1z"/></svg>0400 123 456</li>
      <li><svg viewBox="0 0 24 24"><path d="M2 5h20v14H2z M2 5l10 8 10-8" /></svg>daniel@harborbuilders.com.au</li>
      <li><svg viewBox="0 0 24 24"><circle cx="12" cy="12" r="10"/></svg>www.harborbuilders.com.au</li>
    </ul>

    <div class="address">
      <p>PO Box 1180 Northgate</p>
      <p>LPO Bayview WA 6100</p>
      <p><span class="label">Reg:</span> 10482 | <span class="label">ABN:</span> 12 345 678 901</p>
    </div>

    <div class="edge-tab"></div>
    <svg class="base-band" viewBox="0 0 700 22" preserveAspectRatio="none" aria-hidden="true">
      <polygon points="0,8 400,8 392,22 0,22" fill="var(--navy)"/>
      <polygon points="408,0 700,0 700,22 400,22" fill="var(--orange)"/>
    </svg>
  </section>
</body>
</html>
```